Nanny Share Ecommerce Website for Finding Childcare and Parents who need Childcare BrightPramHub.net

Our company needs an ecommerce website (BrightPramHub.net) for a US subscription based service strictly for nanny sharing that connects families and caregivers. The website would allow families to connect with one another as well as to search for nannies. The service would be searchable for other families by location (by radius or zip code), children demographic (age range/gender/special needs), days of week or times, after school care, school closure days (holidays), etc. The service would also be searchable for nannies based on gender, provider age range, years experience, language, hourly rate, transportation available, certification (CPR first aid), education etc. The search fields would be searchable and sortable and allow to connect with the provider (after paying subscription fee). The service would be similar to tendlyfolk.net in that it would allow for families and caregivers to post photos as well as a short bio of the themselves. There would also be a feedback/star rating mechanism to rate caregivers who have performed work for families (viewable to public). The service would be free for nannies to post their bios and only a subscription based service for families to connect with other families or with caregivers (able to view bio but need service to connect). There will be a short bio on the benefits of nanny sharing (reduced cost, increased flexibility for parents, reduced illness, increased socialization with other children vs. sole nanny), as well as Q&A section with best practices.

Target Market(s)

Families, Nannies

Industry/Entity Type

Childcare

Logo Text

Bright Pram Hub

Coding

Coded - Design and coding required

Number of Pages Required

5+ page

Requirements
Must have
• Searchable (need to be able to search for families as well as nannies), responsive, functional, easy to use, add value to families and nannies. Needs to be able to collect payment for subscription.
Nice to have
• Optimized for mobile, SEO optimized

```html
<!DOCTYPE html>
<html lang="en">
<head>
<meta charset="utf-8">
<title>Bright Pram Hub — Nanny Share</title>
<link rel="stylesheet" href="https://fonts.googleapis.com/css2?family=Poppins:wght@400;500;600&family=Roboto:ital,wght@0,400;0,500;0,700;1,400;1,700&display=swap">
<style>
:root{
  --pink:#e65f6e;
  --pink-soft:#fdeaed;
  --cyan:#12b4e3;
  --cyan-deep:#0aa6d6;
  --ink:#222;
  --muted:#555;
  --grey-bg:#f2f2f2;
  --dark:#1b1b1b;
  --white:#fff;
}
*{box-sizing:border-box;margin:0;padding:0}
html,body{width:1200px;height:3734px;overflow:hidden}
body{font-family:"Roboto",sans-serif;color:var(--ink);background:var(--white);position:relative}
.btn{display:inline-block;background:var(--pink);color:var(--white);font:500 14px "Roboto",sans-serif;padding:11px 18px;border-radius:4px;text-decoration:none}
.eyebrow{color:var(--cyan);font-size:15px}
.title{color:var(--pink);font:700 34px "Roboto",sans-serif}
.center{text-align:center}
p.body{font-size:13px;line-height:21px;color:var(--ink)}

/* header */
.site-header{height:92px;position:relative}
.brand{position:absolute;left:100px;top:24px;display:flex;align-items:center;gap:10px;color:var(--pink);font:600 22px "Poppins",sans-serif;text-decoration:none}
.brand-dot{width:34px;height:34px;border-radius:50%;background:var(--cyan)}
.join{position:absolute;right:100px;top:12px;padding:6px 16px;font-size:14px}
.nav{position:absolute;right:100px;top:54px;display:flex;gap:28px;list-style:none;font-size:15px}
.nav a{color:var(--ink);text-decoration:none}
.nav a.active{color:var(--pink)}

/* hero */
.hero{height:518px;position:relative;background:linear-gradient(100deg,#b9b6ae 0%,#d9cfc4 40%,#e8dccd 70%,#c7c2bd 100%)}
.hero-copy{position:absolute;left:120px;top:160px;color:var(--white)}
.hero-copy h1{font:500 46px "Poppins",sans-serif;margin-bottom:18px}
.hero-copy h2{font:700 24px/42px "Roboto",sans-serif;margin-bottom:16px}
.hero-arrow{position:absolute;top:235px}
.hero-arrow.left{left:36px}.hero-arrow.right{right:36px}

/* about */
.about{height:403px;position:relative}
.finder{position:absolute;left:124px;top:85px;width:396px;height:229px;background:var(--cyan);border-radius:12px;color:var(--white);padding:26px 20px}
.finder-head{display:flex;gap:26px;align-items:center;padding-left:22px;border-bottom:2px solid rgba(255,255,255,.7);padding-bottom:16px}
.finder-head small{display:block;font-size:14px}
.finder-head strong{font:500 27px "Roboto",sans-serif}
.finder-form{margin-top:14px;background:var(--white);border-radius:3px;height:40px;display:flex;justify-content:space-between;align-items:center;padding:0 12px;font-size:12px;color:#999}
.finder-form b{color:var(--pink);font-size:18px}
.finder-note{font-size:11px;text-align:center;margin-top:12px}
.finder-note u{font-weight:700}
.about-copy{position:absolute;left:565px;top:100px;width:525px}
.about-copy .eyebrow{display:block;margin-bottom:4px}
.about-copy p{margin:14px 0 18px}

/* services */
.services{height:673px;background:var(--pink-soft);position:relative}
.services .head{padding-top:88px}
.services .eyebrow{display:block;margin-bottom:4px}
.tile{position:absolute;overflow:hidden}
.tile span{position:absolute;font:600 18px "Poppins",sans-serif;color:#222}
.tile.child{left:124px;top:172px;width:498px;height:414px;background:linear-gradient(135deg,#c9a57e,#d5c4b0 50%,#b07f6a)}
.child-frame{position:absolute;left:34px;top:30px;width:428px;height:355px;border:3px solid var(--pink);background:rgba(60,40,40,.55);color:var(--white);text-align:center;padding-top:88px}
.child-frame h3{font:600 24px "Poppins",sans-serif;margin-bottom:14px}
.child-frame p{font-size:13px;line-height:22px;width:390px;margin:0 auto 20px}
.child-frame a{color:var(--white);font:500 14px "Poppins",sans-serif}
.tile.senior{left:640px;top:172px;width:428px;height:197px;background:linear-gradient(120deg,#c8c0b6,#e7ddd3 60%,#a8b9a0)}
.tile.senior span{left:16px;top:22px}
.tile.pet{left:640px;top:387px;width:204px;height:199px;background:linear-gradient(160deg,#9fb4c3,#c49a6c 70%)}
.tile.home{left:862px;top:387px;width:206px;height:199px;background:linear-gradient(160deg,#a9a4a0,#c9a8a0 60%,#d98e8a)}
.tile.pet span,.tile.home span{bottom:10px;left:0;right:0;text-align:center}

/* agency */
.agency{height:443px;position:relative;overflow:hidden}
.agency-photo{position:absolute;left:700px;top:7px;width:500px;height:436px;background:radial-gradient(ellipse at 50% 50%,#f1d9c4 0%,#eee6dc 45%,#fff 75%)}
.agency-copy{position:absolute;left:124px;top:78px;width:565px;z-index:1}
.agency-copy h2{font:700 30px/40px "Roboto",sans-serif;color:var(--pink);margin:6px 0 12px}
.agency-copy p{margin-bottom:24px}

/* benefits */
.benefits{height:386px;background:linear-gradient(100deg,#d7606d 0%,#b06478 45%,#6c84a2 100%);color:var(--white);text-align:center}
.benefits .head{padding-top:80px}
.benefits .head small{font-size:15px}
.benefits .head h2{font:700 34px "Roboto",sans-serif;margin-top:4px}
.benefit-row{display:flex;justify-content:center;margin-top:40px}
.benefit{width:212px;border-left:1px solid rgba(255,255,255,.55);padding:4px 10px}
.benefit:first-child{border-left:none}
.benefit svg{height:54px}
.benefit p{font-size:15px;line-height:25px;margin-top:8px}

/* testimonials */
.testimonials{height:391px;position:relative}
.testimonials .head{padding-top:80px}
.testimonials h2{font:700 34px "Roboto",sans-serif;color:var(--pink)}
.quote{position:absolute;top:170px;width:440px;display:flex;gap:14px}
.quote.a{left:120px}.quote.b{left:643px}
.quote-mark{color:var(--pink);font:700 60px/46px "Poppins",sans-serif}
.quote p{font:italic 700 12.5px/21px "Roboto",sans-serif}
.quote cite{display:block;text-align:right;font:400 17px "Roboto",sans-serif;font-style:normal;margin-top:12px}
.stars{text-align:right;color:var(--cyan);font-size:14px;letter-spacing:1px}

/* faq */
.faq{height:463px;background:var(--grey-bg);position:relative}
.faq-art{position:absolute;left:0;top:57px;width:460px;height:324px;border-radius:0 60% 60% 0/0 50% 50% 0;background:linear-gradient(90deg,#d5d84a 0%,#e2338a 45%,#7fcde8 100%);opacity:.85}
.faq-list{position:absolute;left:480px;top:92px;width:645px;list-style:none}
.faq-item{background:var(--white);border:1px solid #ddd;margin-bottom:17px;height:40px;display:flex;align-items:center;justify-content:space-between;padding:0 14px;font:italic 700 13.5px "Roboto",sans-serif}
.faq-item i{width:22px;height:22px;border-radius:50%;background:var(--pink);color:var(--white);font:400 16px/22px "Roboto",sans-serif;text-align:center;font-style:normal}
.faq-item.open{background:var(--cyan);color:var(--white);border-color:var(--cyan);margin-bottom:0}
.faq-item.open i{background:var(--white);color:var(--cyan)}
.faq-answer{background:var(--white);border:1px solid #ddd;border-top:none;height:74px;padding:16px 14px;font-size:13px;line-height:20px;color:var(--muted);margin-bottom:13px}

/* footer */
.site-footer{height:304px;background:var(--cyan);color:var(--white);position:relative}
.f-col{position:absolute;top:58px}
.f-col h4{font:400 19px "Roboto",sans-serif;margin-bottom:20px}
.f-col ul{list-style:none;font-size:12px;line-height:26px}
.f-contact{left:117px;width:220px}
.f-contact li{display:flex;gap:8px;align-items:flex-start;line-height:17px;margin-bottom:12px}
.f-links{left:361px}
.f-hours{left:550px}
.f-hours td{font-size:12px;padding:0 14px 12px 0;vertical-align:top}
.f-sub{left:824px}
.sub-form{display:flex;height:35px}
.sub-form span{width:187px;background:var(--white);color:#444;font-size:12px;line-height:35px;padding-left:10px}
.sub-form b{width:87px;background:var(--pink);font:500 14px/35px "Roboto",sans-serif;text-align:center}
.social{display:flex;gap:8px;margin:18px 0 0 155px}
.social i{width:34px;height:34px;border-radius:3px}
.copyright{height:61px;background:var(--dark);color:#ddd;text-align:center;font-size:12px;line-height:61px}
</style>
</head>
<body>

<header class="site-header">
  <a class="brand" href="#"><span class="brand-dot"></span>Bright Pram Hub</a>
  <a class="btn join" href="#">Join Now</a>
  <ul class="nav">
    <li><a class="active" href="#">Home</a></li>
    <li><a href="#">About</a></li>
    <li><a href="#">Services</a></li>
    <li><a href="#">Our Staffs</a></li>
    <li><a href="#">Pricing</a></li>
    <li><a href="#">Blog</a></li>
    <li><a href="#">Contact Us</a></li>
  </ul>
</header>

<section class="hero" role="img" aria-label="Photo of a mother and young daughter playing with building blocks at a table">
  <svg class="hero-arrow left" width="24" height="48" viewBox="0 0 24 48"><path d="M20 2 4 24l16 22" fill="none" stroke="#fff" stroke-width="2"/></svg>
  <svg class="hero-arrow right" width="24" height="48" viewBox="0 0 24 48"><path d="M4 2l16 22L4 46" fill="none" stroke="#fff" stroke-width="2"/></svg>
  <div class="hero-copy">
    <h1>Bright Pram Hub</h1>
    <h2>Sed Ut Perspiciatis Unde Omnis Iste<br>Natus Error Sit Laudantium</h2>
    <a class="btn" href="#">Find Care</a>
  </div>
</section>

<section class="about">
  <div class="finder">
    <div class="finder-head">
      <svg width="58" height="66" viewBox="0 0 58 66"><circle cx="29" cy="22" r="16" fill="none" stroke="#fff" stroke-width="4"/><path d="M4 64c2-16 12-22 25-22s23 6 25 22z" fill="none" stroke="#fff" stroke-width="4"/></svg>
      <div><small>Search For The</small><strong>Nanny Near You</strong></div>
    </div>
    <div class="finder-form">Enter Your Zip <b>Go!</b></div>
    <p class="finder-note">* Sed ut perspiciatis unde omnis iste natus <u>Details</u></p>
  </div>
  <div class="about-copy">
    <span class="eyebrow">A Little</span>
    <h2 class="title">About Us</h2>
    <p class="body">Lorem ipsum dolor sit amet, consectetur adipiscing elit, sed do eiusmuiy od tempor incididunt ut labore et dolore magna aliqua. Ut enim ad minim veniam, quis nostrud exercitation ullamco laboris nisi ut aliquip ex ea commodo consequat. Lorem ipsum dolor sit amet consectet ut la quis nostrud exercitatio aliqua.</p>
    <a class="btn" href="#">Learn More</a>
  </div>
</section>

<section class="services">
  <div class="head center">
    <span class="eyebrow">What We Offer</span>
    <h2 class="title">Our Services</h2>
  </div>
  <div class="tile child" role="img" aria-label="Photo of children playing with toys in a playroom">
    <div class="child-frame">
      <h3>Child Care</h3>
      <p>Lorem ipsum dolor sit amet, consectetur adipiscing elit, sed do eiusmod tempor incididunt ut labore et dolore magna aliqui exercitation ullamco laboris equat.</p>
      <a href="#">Get Started</a>
    </div>
  </div>
  <div class="tile senior" role="img" aria-label="Photo of a caregiver with an elderly woman"><span>Senior Care</span></div>
  <div class="tile pet" role="img" aria-label="Photo of a dog and a cat resting together"><span>Pet Care</span></div>
  <div class="tile home" role="img" aria-label="Photo of a person cleaning a window"><span>Home Care</span></div>
</section>

<section class="agency">
  <div class="agency-photo" role="img" aria-label="Photo of a smiling mother holding her baby on a yellow exercise ball"></div>
  <div class="agency-copy">
    <span class="eyebrow">Bright Pram Hub</span>
    <h2>We Are More Than Just a<br>Nanny Agency</h2>
    <p class="body">Lorem ipsum dolor sit amet, consectetur adipiscing elit, sed do eiusmuiy od tempor incididunt ut labore et dolore magna aliqua. Ut enim ad minim veniam, quis nostrud exercitation ullamco laboris nisi ut aliquip ex ea commodo consequat. Lorem ipshjeu ulkum oris nisi ut aliquip ex ea commodo dolor sit amet, consectet ut la quis nostrud exercitatio aliqua.</p>
    <a class="btn" href="#">Learn More</a>
  </div>
</section>

<section class="benefits">
  <div class="head">
    <small>Our Benefits</small>
    <h2>Why Choose Us</h2>
  </div>
  <div class="benefit-row">
    <div class="benefit">
      <svg viewBox="0 0 50 54" width="50"><path d="M18 4h14l-5 9h-4z" fill="#fff"/><path d="M21 14c-12 6-17 18-14 28 2 8 10 10 18 10s16-2 18-10c3-10-2-22-14-28z" fill="#fff"/><text x="25" y="43" font-size="20" font-family="Roboto,sans-serif" font-weight="700" fill="#c9626f" text-anchor="middle">$</text></svg>
      <p>Reduced Cost</p>
    </div>
    <div class="benefit">
      <svg viewBox="0 0 70 54" width="70"><circle cx="14" cy="10" r="6" fill="#fff"/><rect x="8" y="18" width="12" height="20" rx="3" fill="#fff"/><circle cx="52" cy="20" r="6" fill="#fff"/><rect x="46" y="28" width="12" height="16" rx="3" fill="#fff"/><rect x="26" y="30" width="14" height="14" fill="#fff"/><rect x="4" y="48" width="62" height="3" fill="#fff"/></svg>
      <p>Increased Socialization<br>With Other Children</p>
    </div>
    <div class="benefit">
      <svg viewBox="0 0 54 54" width="54"><path d="M4 4v46h46" fill="none" stroke="#fff" stroke-width="4"/><rect x="12" y="14" width="7" height="32" fill="#fff"/><rect x="23" y="22" width="7" height="24" fill="#fff"/><rect x="34" y="30" width="7" height="16" fill="#fff"/><path d="M12 8l30 24" stroke="#fff" stroke-width="3"/></svg>
      <p>Reduced Illness</p>
    </div>
    <div class="benefit">
      <svg viewBox="0 0 54 54" width="54"><circle cx="15" cy="8" r="6" fill="#fff"/><path d="M7 16h16v18h-4v18h-8V34H7z" fill="#fff"/><circle cx="39" cy="8" r="6" fill="#fff"/><path d="M31 16h16l3 20h-5v16h-10V36h-5z" fill="#fff"/></svg>
      <p>Increased Flexibility<br>For Parents</p>
    </div>
  </div>
</section>

<section class="testimonials">
  <div class="head center">
    <span class="eyebrow">Testimonials</span>
    <h2>What Our Families Say</h2>
  </div>
  <blockquote class="quote a">
    <span class="quote-mark">&ldquo;</span>
    <div>
      <p>Lorem ipsum dolor sit amet, consectetur adipiscing elit, sed dko eiusmod tempor incididunt ut labore et dolore magna aliqua. Ut enim ad minim veniam, quis nostrud exercitation ullamco laboris nisi ut aliquip ex ea commodo consequat.</p>
      <cite>- Dana Whitfield</cite>
      <div class="stars">★★★★★</div>
    </div>
  </blockquote>
  <blockquote class="quote b">
    <span class="quote-mark">&ldquo;</span>
    <div>
      <p>Lorem ipsum dolor sit amet, consectetur adipiscing elit, sed dko eiusmod tempor incididunt ut labore et dolore magna aliqua. Ut enim ad minim veniam, quis nostrud exercitation ullamco laboris nisi ut aliquip ex ea commodo consequat.</p>
      <cite>- Dana Whitfield</cite>
      <div class="stars">★★★★★</div>
    </div>
  </blockquote>
</section>

<section class="faq">
  <div class="faq-art" role="img" aria-label="Illustration of colourful speech bubbles spelling FAQ"></div>
  <ul class="faq-list">
    <li class="faq-item open">Lorem Ipsum is simply dummy text of the printing and typesetting industry.<i>−</i></li>
    <li class="faq-answer">There are many variations of passages of Lorem Ipsum available, but the majority have suffered alteration in some form, by injected humour.</li>
    <li class="faq-item">Lorem Ipsum is simply dummy text of the printing and typesetting industry.<i>+</i></li>
    <li class="faq-item">Lorem Ipsum is simply dummy text of the printing and typesetting industry.<i>+</i></li>
    <li class="faq-item">Lorem Ipsum is simply dummy text of the printing and typesetting industry.<i>+</i></li>
  </ul>
</section>

<footer class="site-footer">
  <div class="f-col f-contact">
    <h4>Contact Us</h4>
    <ul>
      <li><svg width="10" height="14" viewBox="0 0 10 14"><path d="M5 0a5 5 0 0 0-5 5c0 4 5 9 5 9s5-5 5-9a5 5 0 0 0-5-5z" fill="#fff"/><circle cx="5" cy="5" r="2" fill="#12b4e3"/></svg>901 Lorem Ipsum, Dolor Sit,<br>Amet - 000001</li>
      <li><svg width="12" height="12" viewBox="0 0 12 12"><path d="M2 0l3 3-1.5 2a7 7 0 0 0 3.5 3.5L9 7l3 3-2 2C5 12 0 7 0 2z" fill="#fff"/></svg>+1 888 888 8888</li>
      <li><svg width="13" height="10" viewBox="0 0 13 10"><rect x=".5" y=".5" width="12" height="9" fill="none" stroke="#fff"/><path d="M.5.5l6 5 6-5" fill="none" stroke="#fff"/></svg>info@brightpramhub.net</li>
    </ul>
  </div>
  <div class="f-col f-links">
    <h4>Useful Links</h4>
    <ul><li>Home</li><li>About</li><li>Services</li><li>Our Staffs</li><li>Pricing</li><li>Blog</li><li>Contact Us</li></ul>
  </div>
  <div class="f-col f-hours">
    <h4>Opening Hours</h4>
    <table>
      <tr><td>Mon - Thurs :</td><td>10:00 am - 8:00 pm</td></tr>
      <tr><td>Fri - Sat :</td><td>11:00 am - 8:00 pm</td></tr>
      <tr><td>Sun :</td><td>Closed</td></tr>
    </table>
  </div>
  <div class="f-col f-sub">
    <h4>Subscribe Us</h4>
    <div class="sub-form"><span>Enter Your Email</span><b>Submit</b></div>
    <div class="social">
      <i style="background:#3b5998"></i><i style="background:var(--pink)"></i><i style="background:#555"></i>
    </div>
  </div>
</footer>
<div class="copyright">Copyright © 2018 . All rights reserved.</div>

</body>
</html>
```